****Business Card Design for Quarrystone Development. Design based around attached logo/company name

I’m looking for business card design for my company Quarrystone Development Group,LLC. Design should be professional, sharp and minimal. Outside of the attached logos, greyscale colors for remainder of cards. My thoughts are two-sided card with attached logo on one side and my info on the other but open to one-sided as well with right design.
Target Market(s)
Real estate professionals including banks, private investors, property owners, developers, commercial tenants like Brewlantern, Grovika or Tanquist’s.
Industry/Entity Type
Commercial real estate development and investments.
Contact Information for Business Card
Name, title, email, phone #’s, web address and physical address
Font styles to use
Other font styles liked:
- Helvetica, Garamond, etc
Colors
Designer to choose only greyscale colors for use in the design.
Requirements
Must have
- Attached logo first or second options.
Nice to have
- Two sided card with logo on one side. Attached Logo/company name can be laid out any way that flows as long as it’s legible.name
Should not have
- No loud colors. ***Please do not include logo, I have removed the company design with a logo image.

```html
<!DOCTYPE html>
<html lang="en">
<head>
<meta charset="utf-8">
<title>Quarrystone Development Group – Business Card</title>
<link href="https://fonts.googleapis.com/css2?family=EB+Garamond:wght@400&family=Arimo:wght@400&display=swap" rel="stylesheet">
<style>
  :root {
    --backdrop: #e4e4e4;
    --slate-light: #6a6f7b;
    --slate-dark: #515664;
    --slate-deep: #474b57;
    --paper: #ffffff;
    --ink: #5b5f6b;
    --ink-soft: #6b6e78;
    --rule: #9a9ea8;
  }
  * { margin: 0; padding: 0; box-sizing: border-box; }
  html, body { width: 1200px; height: 1200px; overflow: hidden; background: var(--backdrop); }
  .canvas { position: relative; width: 1200px; height: 1200px; }

  .card {
    position: absolute; left: 262px; width: 686px; height: 392px;
    overflow: hidden;
  }
  .card--front { top: 165px; }
  .card--back  { top: 626px; background: linear-gradient(180deg, var(--slate-light), var(--slate-dark)); }

  .card__shape { position: absolute; inset: 0; width: 100%; height: 100%; }

  .brand { position: absolute; left: 121px; top: 70px; width: 280px; }
  .brand__name {
    font-family: "EB Garamond", Garamond, serif; font-weight: 400;
    font-size: 42px; line-height: 1; color: var(--paper); letter-spacing: 0.5px;
    white-space: nowrap;
  }
  .brand__rule { height: 1px; background: var(--rule); margin-top: 3px; width: 282px; }
  .brand__sub {
    font-family: "EB Garamond", Garamond, serif; font-size: 18px;
    color: var(--slate-deep); letter-spacing: 0.4px; margin-top: 2px; white-space: nowrap;
  }

  .contact {
    position: absolute; right: 36px; top: 172px; text-align: right;
    font-family: Arimo, Helvetica, Arial, sans-serif; color: var(--ink-soft);
  }
  .contact__name {
    font-family: "EB Garamond", Garamond, serif; font-size: 22px;
    color: var(--ink); letter-spacing: 0.6px; line-height: 1.1;
  }
  .contact__title { font-size: 14.5px; line-height: 1.3; }
  .contact__address { font-size: 14.5px; line-height: 20px; margin-top: 14px; }
  .contact__lines { list-style: none; margin-top: 14px; font-size: 14.5px; }
  .contact__lines li { display: flex; justify-content: flex-end; align-items: center; height: 19.5px; }
  .contact__lines svg { width: 11px; height: 11px; margin-left: 11px; fill: var(--ink); }

  .back__pattern {
    position: absolute; left: 30px; top: 10px; right: 0; bottom: 10px;
    background: linear-gradient(90deg, rgba(255,255,255,0.05), rgba(0,0,0,0.08));
  }
  .back__name {
    position: absolute; left: 528px; top: 298px;
    font-family: "EB Garamond", Garamond, serif; font-size: 15px;
    color: var(--paper); letter-spacing: 0.5px;
  }
</style>
</head>
<body>
<main class="canvas">

  <section class="card card--front" aria-label="Business card front">
    <svg class="card__shape" viewBox="0 0 800 457" preserveAspectRatio="none" aria-hidden="true">
      <defs>
        <linearGradient id="slate" x1="0" y1="0" x2="0" y2="1">
          <stop offset="0" stop-color="#6a6f7b"/>
          <stop offset="1" stop-color="#515664"/>
        </linearGradient>
      </defs>
      <rect width="800" height="457" fill="#ffffff"/>
      <path d="M0 0 H662 C600 150 420 390 124 457 H0 Z" fill="url(#slate)"/>
      <path d="M636 0 C580 150 410 380 150 457" fill="none" stroke="#5f6470" stroke-width="3" opacity="0.6"/>
    </svg>

    <div class="brand">
      <div class="brand__name">QUARRYSTONE</div>
      <div class="brand__rule"></div>
      <div class="brand__sub">DEVELOPMENT GROUP, LLC</div>
    </div>

    <div class="contact">
      <div class="contact__name">DANIEL HARROW</div>
      <div class="contact__title">President</div>
      <div class="contact__address">4120 Larkspur Court<br>Fairbanks, Alaska 34810</div>
      <ul class="contact__lines">
        <li>369-480-2176
          <svg viewBox="0 0 12 12" aria-hidden="true"><path d="M2.5 0.5 L4.5 0.5 L5.2 3.2 L3.8 4.3 C4.5 5.8 6 7.4 7.7 8.2 L8.8 6.8 L11.5 7.5 L11.5 9.5 C11.5 10.8 10.5 11.5 9.3 11.3 C4.8 10.5 1.5 7.2 0.7 2.7 C0.5 1.5 1.2 0.5 2.5 0.5 Z"/></svg></li>
        <li>369-480-2190
          <svg viewBox="0 0 12 12" aria-hidden="true"><rect x="3" y="0.5" width="6" height="3"/><rect x="0.5" y="4" width="11" height="5" rx="1"/><rect x="3" y="8" width="6" height="3.5" fill="#fff" stroke="#5b5f6b" stroke-width="1"/></svg></li>
        <li>name@quarrystone.com
          <svg viewBox="0 0 12 12" aria-hidden="true"><rect x="0.5" y="2.5" width="11" height="7.5"/><path d="M0.5 2.8 L6 7 L11.5 2.8" fill="none" stroke="#fff" stroke-width="1"/></svg></li>
        <li>www.quarrystone.com
          <svg viewBox="0 0 12 12" aria-hidden="true"><circle cx="6" cy="6" r="5.5"/><path d="M3 3.5 C4.5 4 4 6 5.5 6.5 C6.5 7 6 9 7 10 M8 2 C8.5 3 9.5 3.5 10 4.5" fill="none" stroke="#fff" stroke-width="1"/></svg></li>
      </ul>
    </div>
  </section>

  <section class="card card--back" aria-label="Business card back">
    <div class="back__pattern" role="img" aria-label="Embossed repeating brand pattern across the card back"></div>
    <div class="back__name">QUARRYSTONE</div>
  </section>

</main>
</body>
</html>
```